Business Card Design Project

- makeup artist business card

- original and creative

- Elegant design

- Feel free to come out with cool designs but stick to being elegant and attractive

- Design relates to makeup

- includes name, occupation, contact numbers, email, website

- regular size business card

- round corner card

- double sided

- on 1 side it should just have the website name in the center " moonveilstudio.net "

Industry/Entity Type

Business

Requirements
Must have
• Delia Marsh
Makeup Artist
USA: +1 (415)772-0461
Singapore: +65 82307915
deliamarsh@moonveilstudio.net
www.moonveilstudio.net
Should not have
• nothing cartoon looking.
Pictures of makeup being grab from the internet.. Examples: eyes or lips.

```html
<!DOCTYPE html>
<html lang="en">
<head>
<meta charset="utf-8">
<title>Moon Veil Studio – Business Cards</title>
<link href="https://fonts.googleapis.com/css2?family=Arimo:wght@400;700&family=Tinos:ital,wght@0,700;1,400&display=swap" rel="stylesheet">
<style>
  :root {
    --bg: #f3e6ec;
    --plum: #8a1f62;
    --plum-light: #a9387a;
    --plum-deep: #6f1450;
    --rose: #c94a93;
    --rose-soft: #e6a3c8;
    --ghost: rgba(255, 255, 255, 0.16);
    --white: #ffffff;
    --ink: #2a2a2a;
    --brand: #8c2a6e;
  }
  * { margin: 0; padding: 0; box-sizing: border-box; }
  html, body { width: 1200px; height: 951px; overflow: hidden; }
  body {
    background: var(--bg);
    font-family: "Arimo", Arial, sans-serif;
    position: relative;
  }
  .card {
    position: absolute;
    width: 620px;
    height: 354px;
    border-radius: 30px;
    overflow: hidden;
  }

  /* Back side */
  .card-back {
    left: 70px; top: 80px;
    background: linear-gradient(120deg, var(--plum-deep), var(--plum) 45%, var(--plum-light));
  }
  .card-back .edges { position: absolute; inset: 0; }
  .back-name {
    position: absolute;
    left: 110px; top: 110px;
    font-size: 46px;
    font-weight: 400;
    line-height: 1;
    color: var(--ghost);
    white-space: nowrap;
  }
  .back-site {
    position: absolute;
    left: 110px; top: 262px;
    display: flex; align-items: center; gap: 14px;
    color: var(--white);
    font-size: 25px;
    letter-spacing: 1.5px;
    white-space: nowrap;
  }
  .dots { display: flex; align-items: center; gap: 9px; }
  .dots i { display: block; background: var(--white); border-radius: 50%; }

  /* Front side */
  .card-front {
    left: 510px; top: 500px;
    background: var(--white);
    box-shadow: 0 0 0 1px rgba(0,0,0,0.04);
  }
  .brand-name {
    position: absolute;
    left: 40px; top: 66px;
    display: flex; align-items: center; gap: 10px;
    font-size: 34px;
    font-weight: 400;
    line-height: 1;
    color: var(--brand);
    white-space: nowrap;
  }
  .brand-name .dot {
    width: 12px; height: 12px;
    border-radius: 50%;
    background: var(--brand);
  }
  .person {
    position: absolute;
    right: 34px; top: 62px;
  }
  .person .name {
    font-family: "Tinos", "Times New Roman", serif;
    font-weight: 700;
    font-size: 22px;
    color: var(--ink);
  }
  .person .role {
    font-family: "Tinos", "Times New Roman", serif;
    font-style: italic;
    font-size: 15px;
    color: var(--rose);
    margin-top: 2px;
  }
  .contacts {
    position: absolute;
    top: 198px;
    font-size: 15px;
    color: var(--ink);
    line-height: 1.45;
  }
  .contacts.phones { left: 36px; }
  .contacts.online { left: 300px; top: 214px; }
  .contacts li { list-style: none; display: flex; align-items: center; gap: 8px; white-space: nowrap; }
  .contacts svg { flex: none; }
  .site-accent { color: var(--rose); }
  .band { position: absolute; left: 0; bottom: 0; }
</style>
</head>
<body>

  <section class="card card-back" aria-label="Business card, back">
    <svg class="edges" width="620" height="354" viewBox="0 0 620 354" aria-hidden="true">
      <defs>
        <linearGradient id="edgeSheen" x1="0" x2="1">
          <stop offset="0" stop-color="#c34d8e"/>
          <stop offset="0.55" stop-color="#f4dbe8"/>
          <stop offset="1" stop-color="#b13f80"/>
        </linearGradient>
      </defs>
      <path d="M0 0 H48 Q22 177 48 354 H0 Z" fill="url(#edgeSheen)"/>
      <path d="M48 0 Q22 177 48 354" stroke="#ffffff" stroke-width="2" fill="none" opacity="0.8"/>
      <path d="M620 0 H575 Q600 177 575 354 H620 Z" fill="url(#edgeSheen)"/>
      <path d="M575 0 Q600 177 575 354" stroke="#ffffff" stroke-width="2" fill="none" opacity="0.8"/>
    </svg>
    <div class="back-name" aria-hidden="true">moon veil studio</div>
    <div class="back-site">
      <span class="dots" aria-hidden="true">
        <i style="width:3px;height:3px"></i>
        <i style="width:4px;height:4px"></i>
        <i style="width:5px;height:5px"></i>
        <i style="width:6px;height:6px"></i>
        <i style="width:8px;height:8px"></i>
      </span>
      <span>www.moonveilstudio.net</span>
    </div>
  </section>

  <section class="card card-front" aria-label="Business card, front">
    <div class="brand-name">
      <span class="dot" aria-hidden="true"></span>
      <span>moon veil studio</span>
    </div>
    <div class="person">
      <div class="name">Delia Marsh</div>
      <div class="role">Makeup Artist</div>
    </div>

    <ul class="contacts phones">
      <li>
        <svg width="14" height="14" viewBox="0 0 14 14" aria-hidden="true"><circle cx="7" cy="7" r="6" fill="none" stroke="#c94a93" stroke-width="1.5"/><path d="M5 4 Q3.5 7 5 10" stroke="#c94a93" stroke-width="1.8" fill="none"/></svg>
        USA: +1 (415)772-0461
      </li>
      <li>
        <svg width="14" height="14" viewBox="0 0 14 14" aria-hidden="true"><circle cx="7" cy="7" r="6" fill="none" stroke="#c94a93" stroke-width="1.5"/><path d="M5 4 Q3.5 7 5 10" stroke="#c94a93" stroke-width="1.8" fill="none"/></svg>
        Singapore: +65 82307915
      </li>
    </ul>

    <ul class="contacts online">
      <li>
        <svg width="14" height="14" viewBox="0 0 14 14" aria-hidden="true"><circle cx="7" cy="7" r="6" fill="none" stroke="#c94a93" stroke-width="1.5"/><rect x="4" y="5" width="6" height="4" fill="#c94a93"/></svg>
        deliamarsh@moonveilstudio.net
      </li>
      <li>
        <svg width="14" height="14" viewBox="0 0 14 14" aria-hidden="true"><circle cx="7" cy="7" r="6" fill="#c94a93"/></svg>
        <span>www.<span class="site-accent">moonveilstudio</span>.net</span>
      </li>
    </ul>

    <svg class="band" width="620" height="110" viewBox="0 0 620 110" aria-hidden="true">
      <defs>
        <linearGradient id="bandFill" x1="0" x2="1">
          <stop offset="0" stop-color="#6f1450"/>
          <stop offset="0.5" stop-color="#9a2c6c"/>
          <stop offset="1" stop-color="#c94a93"/>
        </linearGradient>
      </defs>
      <path d="M0 62 Q260 40 620 46 V110 H0 Z" fill="#e6a3c8"/>
      <path d="M0 78 Q300 52 620 58 V110 H0 Z" fill="url(#bandFill)"/>
      <path d="M0 78 Q300 52 620 58" stroke="#ffffff" stroke-width="2" fill="none"/>
    </svg>
  </section>

</body>
</html>
```